Google Form Graphic to suit our Brand and industry

Create a graphic / image for us to put at the top of our client enquiry google form.
The image will be a section of an architectural home with our branding over the top. Preferably translucent.
The image must suit the shape of the google forms image, which is an elongated rectangle
#003d5d - brand colour

Target Market(s)

residential home owners, high end architectural homes

Industry/Entity Type

Residential construction

Colors
0054AA
0677BA
7BADD7
CADEEF
E8F1F8

Requirements
Must have
• our branding and a photo of an architectural home in the background

```html
<!DOCTYPE html>
<html lang="en">
<head>
<meta charset="utf-8">
<title>New Client Enquiry Form</title>
<link href="https://fonts.googleapis.com/css2?family=Montserrat:wght@500&family=Roboto:wght@400;500&display=swap" rel="stylesheet">
<style>
  :root {
    --page-bg: #f7efdf;
    --card-bg: #ffffff;
    --card-border: #e2ddd2;
    --ink: #202124;
    --ink-soft: #5f6368;
    --hint: #70757a;
    --accent-blue: #4285f4;
    --brand-navy: #003d5d;
    --title-rule: #8a7550;
    --required: #d93025;
    --tab-gold: #e3bd63;
    --tab-ink: #3c2f12;
  }
  * { box-sizing: border-box; margin: 0; padding: 0; }
  html, body { width: 862px; height: 1200px; overflow: hidden; }
  body {
    position: relative;
    background: var(--page-bg);
    font-family: "Roboto", Arial, sans-serif;
    color: var(--ink);
  }
  .header-banner {
    position: absolute; left: 34px; top: 11px; width: 797px; height: 199px;
    border-radius: 6px; overflow: hidden;
  }
  .header-photo {
    position: absolute; inset: 0;
    background: linear-gradient(100deg, #0f2f4a 0%, #1b4466 40%, #5a6268 52%, #8a8d90 72%, #3e4143 100%);
  }
  .header-brand {
    position: absolute; left: 0; right: 0; top: 80px;
    text-align: center;
    font-family: "Montserrat", Arial, sans-serif; font-weight: 500;
    font-size: 48px; letter-spacing: 1px; color: #ffffff;
  }
  .card {
    position: absolute; left: 34px; width: 791px;
    background: var(--card-bg);
    border: 1px solid var(--card-border);
    border-radius: 6px;
  }
  .title-card { top: 272px; height: 171px; border-top: none; border-radius: 0 0 6px 6px; }
  .form-title {
    position: absolute; left: 25px; top: 22px;
    font-size: 32px; font-weight: 400; color: var(--ink);
  }
  .title-rule {
    position: absolute; left: 25px; top: 70px; width: 654px; height: 2px;
    background: var(--title-rule);
  }
  .toolbar { position: absolute; left: 38px; top: 84px; display: flex; gap: 18px; }
  .toolbar svg { width: 23px; height: 23px; }
  .card-actions { position: absolute; right: 30px; top: 26px; display: flex; gap: 34px; }
  .form-description {
    position: absolute; left: 25px; top: 126px;
    font-size: 14.5px; color: var(--ink);
  }
  .question-card { height: 141px; }
  .question-card.active { border-left: 5px solid var(--accent-blue); }
  .question-label {
    position: absolute; left: 25px; top: 26px; font-size: 16px; color: var(--ink);
  }
  .active .question-label { left: 28px; }
  .required-mark { color: var(--required); margin-left: 8px; }
  .answer-hint {
    position: absolute; left: 25px; top: 74px;
    font-size: 13.5px; color: var(--hint); letter-spacing: 0.3px;
  }
  .active .answer-hint { left: 20px; }
  .answer-line {
    position: absolute; left: 25px; top: 97px; width: 370px;
    border-bottom: 1px dotted #9aa0a6;
  }
  .active .answer-line { left: 20px; }
  .section-nav {
    position: absolute; left: 34px; top: 1084px;
    font-size: 13.5px; color: var(--ink-soft);
    display: flex; align-items: center;
  }
  .section-nav .nav-choice { margin-left: 18px; color: var(--ink); width: 318px; }
  .section-divider {
    position: absolute; left: 835px; top: 1087px; width: 1px; height: 113px;
    background: #d7d2c6;
  }
  .section-tab {
    position: absolute; left: 33px; top: 1165px; width: 125px; height: 40px;
    background: var(--tab-gold); border-radius: 6px 6px 0 0;
    font-size: 13.5px; color: var(--tab-ink);
    padding: 9px 0 0 16px;
  }
</style>
</head>
<body>

<div class="header-banner">
  <div class="header-photo" role="img" aria-label="Photograph of an architectural home with tropical palms, tinted navy on the left and greyscale on the right"></div>
  <div class="header-brand">VANTA BUILD</div>
</div>

<section class="card title-card">
  <h1 class="form-title">New Client Enquiry Form</h1>
  <div class="title-rule"></div>
  <div class="toolbar">
    <svg viewBox="0 0 24 24" aria-label="Bold"><text x="5" y="18" font-family="Roboto, sans-serif" font-weight="500" font-size="18" fill="#5f6368">B</text></svg>
    <svg viewBox="0 0 24 24" aria-label="Italic"><text x="7" y="18" font-family="Roboto, sans-serif" font-style="italic" font-size="18" fill="#5f6368">I</text></svg>
    <svg viewBox="0 0 24 24" aria-label="Underline"><text x="5" y="16" font-family="Roboto, sans-serif" font-size="17" fill="#5f6368">U</text><rect x="5" y="19" width="13" height="1.6" fill="#5f6368"/></svg>
    <svg viewBox="0 0 24 24" aria-label="Link"><rect x="2" y="8" width="10" height="8" rx="4" fill="none" stroke="#5f6368" stroke-width="2"/><rect x="12" y="8" width="10" height="8" rx="4" fill="none" stroke="#5f6368" stroke-width="2"/><line x1="8" y1="12" x2="16" y2="12" stroke="#5f6368" stroke-width="2"/></svg>
    <svg viewBox="0 0 24 24" aria-label="Clear formatting"><path d="M4 5h15M11 5l-3 15M5 9l14 12" stroke="#5f6368" stroke-width="2" fill="none"/></svg>
  </div>
  <div class="card-actions">
    <svg width="14" height="20" viewBox="0 0 14 20" aria-label="Collapse"><path d="M3 2l4 4 4-4M3 18l4-4 4 4" stroke="#5f6368" stroke-width="1.8" fill="none"/></svg>
    <svg width="6" height="20" viewBox="0 0 6 20" aria-label="More"><circle cx="3" cy="3" r="2" fill="#5f6368"/><circle cx="3" cy="10" r="2" fill="#5f6368"/><circle cx="3" cy="17" r="2" fill="#5f6368"/></svg>
  </div>
  <p class="form-description">We would love to hear your thoughts or feedback on how we can improve your experience!</p>
</section>

<section class="card question-card active" style="top:458px">
  <p class="question-label">Firstly, how did you hear about us?<span class="required-mark">*</span></p>
  <p class="answer-hint">Short answer text</p>
  <div class="answer-line"></div>
</section>

<section class="card question-card" style="top:614px">
  <p class="question-label">Name</p>
  <p class="answer-hint">Short answer text</p>
  <div class="answer-line"></div>
</section>

<section class="card question-card" style="top:769px">
  <p class="question-label">Phone</p>
  <p class="answer-hint">Short answer text</p>
  <div class="answer-line"></div>
</section>

<section class="card question-card" style="top:924px">
  <p class="question-label">Email</p>
  <p class="answer-hint">Short answer text</p>
  <div class="answer-line"></div>
</section>

<div class="section-nav">
  <span>After section 1</span>
  <span class="nav-choice">Continue to next section</span>
  <svg width="10" height="6" viewBox="0 0 10 6" aria-label="Open menu"><path d="M0 0h10L5 6z" fill="#5f6368"/></svg>
</div>
<div class="section-divider"></div>

<div class="section-tab">Section 2 of 4</div>

</body>
</html>
```